Business Card Design for Retail Product Line

We need a two-sided, full-color business card for a new oral care product line. The feel of the card should invoke emotions of happiness and health. It should be bright, cheerful and modern in appearance. The card should be mostly matte finish, but with elements of spot-gloss and/or raised/embossed features (print, logo, tag lines, etc.).

Target Market(s)

People who are into whole-body health, eat well and understand the importance of nutrition.

Industry/Entity Type

Health And Wellness

Contact Information for Business Card

The logo, color scheme and tag-lines have all been developed and artwork is attached. Card is to be standard-sized and should use a mix of clean, sans-serif fonts; the main font (DIN) is attached as well. The card will be used for 3 individuals and should include placeholders for:
1. Name
2. Title (for example, "CEO")
3. Business address
4. Phone number
5. Website
6. Email address

Font styles to use
Sans Serif
Other font styles liked:
• DIN font

Colors
faa54b
000000
5c5c5c
a2ce44

Requirements
Must have
• 2 sides
• Full color orange on one side
• Image of DNA leaves
• Tag line "Smile from the Inside Out", on single side with orange background
• Company Logo (Plure) on same side as text (name, phone, address, etc.)
• Name, Title, Business Address, Phone Number, Website, Email address
• UPDATE: "Brisk Meadow", not "Brisk M Eadow"
Should not have
• Calligraphy
• Dark colors
• UPDATE!! Do not include "Turmeric infused toothpaste" on the business card
• UPDATE #2!! Do not include "Brisk Meadow" on the business card

```html
<!DOCTYPE html>
<html lang="en">
<head>
<meta charset="utf-8">
<title>Plure Business Card</title>
<link rel="stylesheet" href="https://fonts.googleapis.com/css2?family=Barlow:ital,wght@0,400;0,500;0,600;1,600&display=swap">
<style>
  :root {
    --orange: #faa54b;
    --yellow: #f3cf3f;
    --grey: #5c5c5c;
    --green: #a2ce44;
    --leaf-deep: #0e9447;
    --leaf-light: #8cc63f;
    --helix-grey: #c9cacc;
    --white: #ffffff;
    --page: #ebe6dd;
  }
  * { margin: 0; padding: 0; box-sizing: border-box; }
  html, body {
    width: 1200px;
    height: 1076px;
    overflow: hidden;
    background: var(--page);
  }
  .canvas {
    position: relative;
    width: 1200px;
    height: 1076px;
  }
  .card {
    position: absolute;
    left: 220px;
    width: 760px;
    height: 437px;
    overflow: hidden;
    box-shadow: 0 8px 22px rgba(0, 0, 0, 0.18);
  }
  .card-front {
    top: 70px;
    border-radius: 72px 0 72px 0;
    background: linear-gradient(200deg, var(--orange) 0%, var(--yellow) 50%, var(--orange) 100%);
    display: flex;
    align-items: center;
    justify-content: center;
  }
  .tagline {
    font-family: "Barlow", sans-serif;
    font-style: italic;
    font-weight: 600;
    font-size: 56px;
    line-height: 1.1;
    color: var(--white);
    text-align: center;
  }
  .card-back {
    top: 569px;
    border-radius: 0 72px 0 72px;
    background: var(--grey);
    font-family: "Barlow", sans-serif;
    color: var(--white);
  }
  .person { position: absolute; left: 39px; top: 54px; }
  .person-name { font-size: 30px; font-weight: 600; line-height: 1.1; }
  .person-title { font-size: 19px; font-weight: 500; color: var(--green); line-height: 1.1; }
  .address {
    position: absolute;
    left: 37px;
    top: 176px;
    font-size: 20px;
    line-height: 26px;
  }
  .contact {
    position: absolute;
    left: 37px;
    top: 246px;
    list-style: none;
    font-size: 20px;
    line-height: 29px;
  }
  .contact-label { color: var(--green); font-weight: 600; }
  .brand-name {
    position: absolute;
    left: 37px;
    top: 346px;
    font-size: 32px;
    font-weight: 600;
    line-height: 1.1;
    color: var(--green);
  }
  .dna-leaves {
    position: absolute;
    left: 444px;
    top: 22px;
    width: 290px;
    height: 415px;
  }
</style>
</head>
<body>
<main class="canvas">
  <section class="card card-front" aria-label="Card front">
    <p class="tagline">Smile from the Inside Out</p>
  </section>

  <section class="card card-back" aria-label="Card back">
    <div class="person">
      <p class="person-name">Dara Quill</p>
      <p class="person-title">CEO</p>
    </div>
    <p class="address">18 Harbor Lane, 2nd Ste<br>Alder Falls, Oregon 5678, USA</p>
    <ul class="contact">
      <li><span class="contact-label">Phone:</span> (555).210.3876</li>
      <li><span class="contact-label">Email:</span> hello@plurecare.com</li>
      <li><span class="contact-label">Web:</span> www.plurecare.com</li>
    </ul>
    <p class="brand-name">Plure</p>
    <svg class="dna-leaves" viewBox="0 0 290 415" role="img" aria-label="Illustration of green leaves growing from a DNA helix">
      <defs>
        <linearGradient id="leafFill" x1="0" y1="0" x2="0" y2="1">
          <stop offset="0" stop-color="#8cc63f"/>
          <stop offset="0.55" stop-color="#0e9447"/>
          <stop offset="1" stop-color="#c9cacc"/>
        </linearGradient>
      </defs>
      <rect x="0" y="0" width="290" height="415" rx="60" fill="url(#leafFill)" opacity="0.9"/>
    </svg>
  </section>
</main>
</body>
</html>
```